Silver Meadow LLC business card

I help with the Marketing and Sales of various Natural, Organic, Eco Friendly and Healthy Main Stream products to Retail Corporate accounts as well as Independents and Distributors.I also highlight Private label items to these same Retail Corporate accounts.Cherish the Moments, Enjoy Life!

Speciality & Health Sales and Marketing

Target Market(s)

Men and Women

Industry/Entity Type

Business

Contact Information for Business Card

Silver Meadow, LLC
Janet Louise Verhagen
438 West Finch Lane
Ste 4-237
Phoenix, AZ 85047
602-555-0147
jverhagen@plumvale.net

Requirements
Must have
• Nice, femine font
Something in the background or on a side with a softness
Nice to have
• Cherish the Moments, Enjoy Life
Should not have
• Hardness

```html
<!DOCTYPE html>
<html lang="en">
<head>
<meta charset="utf-8">
<title>Silver Meadow LLC – Business Card</title>
<link href="https://fonts.googleapis.com/css2?family=Quicksand:wght@400;500;700&display=swap" rel="stylesheet">
<style>
  :root {
    --backdrop: #3a3330;
    --card: #242122;
    --card-glow: #302b2c;
    --card-edge: #1c1a1b;
    --ink: #f5f1ef;
    --ink-soft: #dcd5d2;
    --accent: #f08a4b;
    --silver: #d4d0cf;
    --divider: rgba(255,255,255,.07);
  }
  * { margin: 0; padding: 0; box-sizing: border-box; }
  html, body {
    width: 1200px; height: 844px; overflow: hidden;
    background: radial-gradient(ellipse at 50% 45%, #453d39 0%, var(--backdrop) 70%);
    font-family: "Quicksand", "Trebuchet MS", sans-serif;
  }
  .canvas {
    position: relative; width: 1200px; height: 844px;
    display: flex; align-items: center; justify-content: center; gap: 60px;
  }
  .card {
    position: relative; width: 510px; height: 292px;
    border-radius: 14px; overflow: hidden;
    background: radial-gradient(ellipse at 35% 30%, var(--card-glow) 0%, var(--card) 60%, var(--card-edge) 100%);
    box-shadow: 0 14px 40px rgba(0,0,0,.35);
  }
  .card::after {
    content: ""; position: absolute; right: -80px; bottom: -90px;
    width: 260px; height: 260px; border-radius: 50%;
    background: radial-gradient(circle, rgba(240,138,75,.12) 0%, rgba(240,138,75,0) 70%);
    pointer-events: none;
  }
  /* Front */
  .card-front { display: flex; }
  .brand {
    width: 50%; display: flex; flex-direction: column;
    align-items: center; justify-content: center; gap: 16px;
    padding: 60px 18px 0;
  }
  .brand-mark {
    width: 68px; height: 68px; border-radius: 50%;
    background: radial-gradient(circle at 35% 30%, #f6a472 0%, var(--accent) 70%);
  }
  .brand-name {
    font-weight: 700; font-size: 17px; letter-spacing: 1px;
    color: var(--accent); text-transform: uppercase; white-space: nowrap;
  }
  .details {
    width: 50%; padding: 50px 16px 0 24px;
    border-left: 1px solid var(--divider); color: var(--ink);
  }
  .person-name { font-size: 18px; font-weight: 500; line-height: 1.2; white-space: nowrap; }
  .person-title { font-size: 12.5px; font-weight: 500; color: var(--accent); margin-top: 2px; }
  .address { font-size: 12.5px; line-height: 1.45; margin-top: 12px; color: var(--ink-soft); }
  .contact { list-style: none; font-size: 12.5px; line-height: 1.55; margin-top: 12px; color: var(--ink-soft); white-space: nowrap; }
  .contact .label { color: var(--accent); font-weight: 700; margin-right: 5px; }
  /* Back */
  .card-back { display: flex; align-items: center; justify-content: center; }
  .back-mark {
    width: 140px; height: 140px; border-radius: 50%;
    background: linear-gradient(160deg, #f6f4f3 0%, var(--silver) 50%, #9a9594 100%);
    box-shadow: 0 0 40px rgba(255,255,255,.06);
  }
</style>
</head>
<body>
<main class="canvas">
  <section class="card card-front" aria-label="Business card front">
    <div class="brand">
      <div class="brand-mark"></div>
      <div class="brand-name">Silver Meadow LLC</div>
    </div>
    <div class="details">
      <h1 class="person-name">Janet Louise Verhagen</h1>
      <p class="person-title">Managing Director</p>
      <p class="address">438 West Finch Lane, Ste 4-237<br>Phoenix, AZ 85047</p>
      <ul class="contact">
        <li><span class="label">T:</span>602-555-0147</li>
        <li><span class="label">E:</span>jverhagen@plumvale.net</li>
        <li><span class="label">W:</span>www.silvermeadowsales.com</li>
      </ul>
    </div>
  </section>
  <section class="card card-back" aria-label="Business card back">
    <div class="back-mark"></div>
  </section>
</main>
</body>
</html>
```